Corbell Lending Partners - Real estate loans - need a business card with a logo

I need a logo and a business card that looks elegant - that looks as if it is a big stablish corporation - We do real estate loans, my goal is to brand myself with colors black background - gold or silver letters - some combination - Name of the company different color than the rest of the card -

```html
<!DOCTYPE html>
<html lang="en">
<head>
<meta charset="utf-8">
<title>Corbell Lending Partners – Business Card</title>
<link href="https://fonts.googleapis.com/css2?family=Arimo:wght@400;700&display=swap" rel="stylesheet">
<style>
  :root {
    --card-black: #0e0e10;
    --gold: #c9a24a;
    --gold-deep: #a88536;
    --silver: #c4c7cc;
    --silver-soft: #9a9da3;
    --stage: #3a3b3f;
  }
  * { margin: 0; padding: 0; box-sizing: border-box; }
  html, body { width: 1200px; height: 786px; overflow: hidden; }
  body {
    background: var(--stage);
    font-family: "Arimo", Arial, sans-serif;
    position: relative;
  }
  .card {
    position: absolute;
    width: 525px;
    height: 300px;
    top: 243px;
    overflow: hidden;
    background: var(--card-black);
    box-shadow: 0 10px 30px rgba(0,0,0,.5);
  }
  .card-front { left: 45px; }
  .card-back { left: 630px; }

  .front-band { position: absolute; left: 0; bottom: 0; width: 525px; height: 300px; }

  .front-wordmark {
    position: absolute;
    left: 40px;
    top: 104px;
    display: flex;
    align-items: center;
    gap: 12px;
    color: var(--gold);
    font-weight: 700;
    text-transform: uppercase;
  }
  .wordmark-square { width: 18px; height: 18px; background: var(--gold); flex: none; }
  .wordmark-text { line-height: 1.1; }
  .wordmark-text .line-main { display: block; font-size: 34px; letter-spacing: 1px; }
  .wordmark-text .line-sub { display: block; font-size: 14.5px; letter-spacing: 2.4px; }

  .front-divider {
    position: absolute;
    left: 282px;
    top: 58px;
    width: 1.5px;
    height: 118px;
    background: var(--silver-soft);
  }
  .contact {
    position: absolute;
    left: 300px;
    top: 52px;
    color: var(--silver);
    font-size: 11.5px;
    line-height: 1.45;
  }
  .contact-name {
    color: var(--silver);
    font-weight: 700;
    font-size: 19px;
    letter-spacing: .5px;
    text-transform: uppercase;
    line-height: 1.1;
  }
  .contact-title { margin-bottom: 4px; color: var(--silver-soft); }
  .contact-row { display: flex; align-items: center; gap: 5px; }
  .contact-row svg { width: 9px; height: 9px; flex: none; }

  .back-wordmark {
    position: absolute;
    left: 0; right: 0;
    top: 98px;
    display: flex;
    justify-content: center;
    align-items: center;
    gap: 14px;
    color: var(--gold);
    font-weight: 700;
    text-transform: uppercase;
  }
  .back-wordmark .wordmark-square { width: 22px; height: 22px; }
  .back-wordmark .line-main { font-size: 44px; }
  .back-wordmark .line-sub { font-size: 18.5px; letter-spacing: 3.2px; }

  .back-web {
    position: absolute;
    left: 30px; right: 30px;
    top: 238px;
    display: flex;
    align-items: center;
    gap: 12px;
    color: var(--silver);
    font-size: 12px;
    letter-spacing: .4px;
  }
  .back-web .rule { flex: 1; height: 1px; background: var(--silver-soft); }
</style>
</head>
<body>

<section class="card card-front" aria-label="Business card front">
  <svg class="front-band" viewBox="0 0 525 300" aria-hidden="true">
    <path d="M0 280 L300 280 C322 280 326 252 348 248 L525 205" fill="none" stroke="var(--silver-soft)" stroke-width="5"/>
    <path d="M0 290 L320 290 C345 290 348 252 378 244 L525 214 L525 300 L0 300 Z" fill="var(--gold-deep)"/>
  </svg>

  <div class="front-wordmark">
    <span class="wordmark-square"></span>
    <span class="wordmark-text">
      <span class="line-main">Corbell</span>
      <span class="line-sub">Lending Partners</span>
    </span>
  </div>

  <div class="front-divider"></div>

  <div class="contact">
    <div class="contact-name">Daniel Harlow</div>
    <div class="contact-title">Founder</div>
    <div>418 Linden Avenue</div>
    <div>Riverton, WA 99001</div>
    <div class="contact-row">
      <svg viewBox="0 0 10 10"><path d="M2 0.5 L3.8 2.6 L2.8 3.8 C3.5 5.3 4.7 6.5 6.2 7.2 L7.4 6.2 L9.5 8 L8.3 9.5 C4.3 9 1 5.7 0.5 1.7 Z" fill="var(--silver)"/></svg>
      <span>555 014 2287</span>
    </div>
    <div class="contact-row">
      <svg viewBox="0 0 10 10"><rect x="0.5" y="1.5" width="9" height="7" fill="none" stroke="var(--silver)"/><path d="M0.5 1.5 L5 5.5 L9.5 1.5" fill="none" stroke="var(--silver)"/></svg>
      <span>info@corbelllending.com</span>
    </div>
    <div class="contact-row">
      <svg viewBox="0 0 10 10"><circle cx="5" cy="5" r="4.5" fill="var(--silver)"/><path d="M0.5 5 H9.5 M5 0.5 V9.5" stroke="var(--card-black)" stroke-width=".7"/></svg>
      <span>www.corbelllending.com</span>
    </div>
  </div>
</section>

<section class="card card-back" aria-label="Business card back">
  <div class="back-wordmark">
    <span class="wordmark-square"></span>
    <span class="wordmark-text">
      <span class="line-main">Corbell</span>
      <span class="line-sub">Lending Partners</span>
    </span>
  </div>
  <div class="back-web">
    <span class="rule"></span>
    <span>www.corbelllending.com</span>
    <span class="rule"></span>
  </div>
</section>

</body>
</html>
```